sydney wedding photography business needs a business card design

we need a business card design for a sydney based wedding photography and videography business. our business name is :golden hour studio and film. our target clients are 24-35 yrs female. our style is candid, organic, natural, dynamic. we are a team of young photographers and videographers, and help brides to create memories that they will cherish for the rest of their lives. the logo will be provided. we want an elegant design that reflects our style, and also want to give a great impression to our clients that we are one of the best studios in sydney and our brand means quality and premium service.

Target Market(s)

bride to be, 24-35 years old, living in sydney and surrunding areas

Industry/Entity Type

Wedding Photography

Contact Information for Business Card

address: 57 tarrant street, glenmore nsw 2047
mobile: 0431872259
phone: (02) 9163 2408
info@tidewillowstudio.net.au
www.tidewillowstudio.net.au
facebook:tidewillowweddings
instagram:tidewillowweddings

Font styles to use
Serif
Sans Serif

Requirements
Nice to have
• maybe add my slogan"memories beyond eternity" if the layout looks good
Should not have
• no black color, not good idea for wedding biz card

```html
<!DOCTYPE html>
<html lang="en">
<head>
<meta charset="utf-8">
<title>Golden Hour Studio and Film — Business Card</title>
<link href="https://fonts.googleapis.com/css2?family=Roboto:wght@400;500&display=swap" rel="stylesheet">
<style>
  :root {
    --backdrop: #8c6c4a;
    --card-ground: #1e2a3c;
    --icon-ink: #1e2a3c;
    --gold: #e9c62c;
    --text-light: #f2f2f2;
    --photo-sky: #c9d3dc;
    --photo-warm: #d8c6a2;
    --shadow: rgba(0, 0, 0, 0.35);
  }
  * { box-sizing: border-box; margin: 0; padding: 0; }
  html, body {
    width: 1200px;
    height: 902px;
    overflow: hidden;
    background: var(--backdrop);
    font-family: "Roboto", Arial, sans-serif;
  }
  .canvas { position: relative; width: 1200px; height: 902px; }

  .card {
    position: absolute;
    width: 620px;
    height: 354px;
    background: var(--card-ground);
    border-radius: 4px;
    box-shadow: 0 14px 30px var(--shadow);
    overflow: hidden;
  }
  .card--front { left: 90px; top: 80px; }
  .card--back { left: 490px; top: 468px; }

  .brand-name {
    color: var(--gold);
    font-weight: 500;
    text-transform: lowercase;
    letter-spacing: 0.04em;
    line-height: 1.15;
  }
  .card--front .brand {
    position: absolute;
    inset: 0;
    display: flex;
    align-items: center;
    justify-content: center;
    padding: 0 40px;
    text-align: center;
  }
  .card--front .brand-name { font-size: 40px; }

  .back-photo { position: absolute; left: 0; top: 0; width: 620px; height: 354px; }

  .card--back .brand {
    position: absolute;
    right: 24px;
    top: 34px;
    width: 232px;
    text-align: center;
  }
  .card--back .brand-name { font-size: 24px; }

  .contact-list {
    position: absolute;
    left: 376px;
    top: 180px;
    list-style: none;
  }
  .contact-item {
    display: flex;
    align-items: center;
    gap: 8px;
    height: 22px;
    color: var(--text-light);
    font-size: 13px;
    font-weight: 400;
    white-space: nowrap;
  }
  .contact-icon {
    width: 15px;
    height: 15px;
    background: var(--gold);
    border-radius: 2px;
    flex: none;
    display: flex;
    align-items: center;
    justify-content: center;
  }
  .contact-icon svg { width: 11px; height: 11px; }
</style>
</head>
<body>
<main class="canvas">

  <section class="card card--front" aria-label="Business card front">
    <div class="brand">
      <span class="brand-name">golden hour studio and film</span>
    </div>
  </section>

  <section class="card card--back" aria-label="Business card back">
    <svg class="back-photo" viewBox="0 0 620 354" xmlns="http://www.w3.org/2000/svg">
      <defs>
        <linearGradient id="photoTone" x1="0" y1="0" x2="1" y2="0.4">
          <stop offset="0" stop-color="#c9d3dc"/>
          <stop offset="0.55" stop-color="#b9c0c6"/>
          <stop offset="1" stop-color="#d8c6a2"/>
        </linearGradient>
      </defs>
      <path role="img" aria-label="Wedding couple embracing outside a building"
            d="M0 0 H300 Q400 170 330 354 H0 Z" fill="url(#photoTone)"/>
      <path d="M300 0 Q400 170 330 354" fill="none" stroke="#e9c62c" stroke-width="4"/>
    </svg>

    <div class="brand">
      <span class="brand-name">golden hour studio and film</span>
    </div>

    <ul class="contact-list">
      <li class="contact-item">
        <span class="contact-icon"><svg viewBox="0 0 12 12"><path d="M2 1 L4 1 L5 3.5 L3.8 4.5 Q5 7 7.5 8.2 L8.5 7 L11 8 L11 10 Q10 11 8.5 11 Q2 9.5 1 3.5 Q1 2 2 1 Z" fill="#1e2a3c"/></svg></span>
        (02) 9163 2408
      </li>
      <li class="contact-item">
        <span class="contact-icon"><svg viewBox="0 0 12 12"><rect x="3.5" y="1" width="5" height="10" rx="1" fill="#1e2a3c"/><rect x="4.5" y="2.5" width="3" height="5.5" fill="#e9c62c"/></svg></span>
        0431872259
      </li>
      <li class="contact-item">
        <span class="contact-icon"><svg viewBox="0 0 12 12"><circle cx="6" cy="6" r="4.5" fill="none" stroke="#1e2a3c" stroke-width="1.2"/><ellipse cx="6" cy="6" rx="2" ry="4.5" fill="none" stroke="#1e2a3c" stroke-width="1"/><line x1="1.5" y1="6" x2="10.5" y2="6" stroke="#1e2a3c" stroke-width="1"/></svg></span>
        www.tidewillowstudio.net.au
      </li>
      <li class="contact-item">
        <span class="contact-icon"><svg viewBox="0 0 12 12"><rect x="1.5" y="3" width="9" height="6.5" fill="none" stroke="#1e2a3c" stroke-width="1.2"/><path d="M1.5 3 L6 7 L10.5 3" fill="none" stroke="#1e2a3c" stroke-width="1.2"/></svg></span>
        info@tidewillowstudio.net.au
      </li>
      <li class="contact-item">
        <span class="contact-icon"><svg viewBox="0 0 12 12"><circle cx="6" cy="6" r="3" fill="#1e2a3c"/></svg></span>
        tidewillowweddings
      </li>
      <li class="contact-item">
        <span class="contact-icon"><svg viewBox="0 0 12 12"><rect x="3" y="3" width="6" height="6" fill="#1e2a3c"/></svg></span>
        tidewillowweddings
      </li>
      <li class="contact-item">
        <span class="contact-icon"><svg viewBox="0 0 12 12"><path d="M6 11 Q2 6.5 2 4.5 A4 4 0 0 1 10 4.5 Q10 6.5 6 11 Z" fill="#1e2a3c"/><circle cx="6" cy="4.5" r="1.4" fill="#e9c62c"/></svg></span>
        57 tarrant street, glenmore nsw 2047
      </li>
    </ul>
  </section>

</main>
</body>
</html>
```